Biz Card

MARKETING today is the most rapidly changing business discipline. Media options to reach customers, actual customer preferences and consumer buying decisions change by the minute . . . no, by the second. The behavioral data generated by all aspects of the business and the new technologies that put the data to work together produce the potential to generate business intelligence and guide smart resource allocation to influence purchase and retention. However, to realize this potential, marketing professionals at all levels and in all organizations must continuously improve their skills not just from on-the-job training but by learning from masters in the field. The Bright Horizon Guild is the training center that serves this professional development need.model logos:msi.orgama.orgcontentmarketinginstitute.comBook covers on MarketingMetrics, Marketing Anaytics
Industry/Entity Type
Business
Contact Information for Business Card
Roy A. YoungCEOMarketing Science Academyphone: 310-601-4755email: roy@marketingscience.comAddress:437 South Rexford DriveBeverly Hills, CA 89377
Look and feel
Each slider illustrates characteristics of the customer's brand and the style your logo design should communicate.

```html
<!DOCTYPE html>
<html lang="en">
<head>
<meta charset="utf-8">
<title>Bright Horizon Guild — Business Card</title>
<link rel="stylesheet" href="https://fonts.googleapis.com/css2?family=Roboto:wght@400;700&family=Roboto+Condensed:wght@700&display=swap">
<style>
  :root {
    --stage: #e7e4e1;
    --card-black: #161616;
    --card-white: #ffffff;
    --brand-red: #8e1d1d;
    --ink: #4a4a4a;
    --ink-soft: #6a6a6a;
    --emboss: #2c2c2c;
    --decor: #ececec;
  }
  * { box-sizing: border-box; margin: 0; padding: 0; }
  html, body { width: 1200px; height: 716px; overflow: hidden; }
  body {
    background: var(--stage);
    font-family: "Roboto", Arial, sans-serif;
    position: relative;
  }
  .card {
    position: absolute;
    top: 209px;
    width: 520px;
    height: 298px;
    border-radius: 3px;
    box-shadow: 0 6px 18px rgba(0,0,0,0.18);
    overflow: hidden;
  }
  .card-back { left: 50px; background: var(--card-black); display: flex; align-items: center; justify-content: center; }
  .card-front { left: 630px; background: var(--card-white); }

  .back-wordmark {
    font-family: "Roboto Condensed", "Arial Narrow", sans-serif;
    font-weight: 700;
    font-size: 34px;
    line-height: 1.05;
    color: var(--emboss);
    text-transform: uppercase;
    text-align: center;
    letter-spacing: 1px;
  }

  .front-wordmark {
    position: absolute;
    left: 34px;
    top: 78px;
    font-family: "Roboto Condensed", "Arial Narrow", sans-serif;
    font-weight: 700;
    font-size: 34px;
    line-height: 1.02;
    color: var(--brand-red);
    text-transform: uppercase;
  }
  .brand-dot {
    position: absolute;
    left: 34px;
    top: 58px;
    width: 12px;
    height: 12px;
    background: var(--brand-red);
  }

  .decor-circle {
    position: absolute;
    right: -40px;
    top: 40px;
    width: 230px;
    height: 230px;
    border-radius: 50%;
    background: var(--decor);
  }

  .contact {
    position: absolute;
    left: 290px;
    top: 64px;
    color: var(--ink);
  }
  .contact-name { font-size: 17px; font-weight: 700; color: var(--brand-red); }
  .contact-title { font-size: 10px; color: var(--ink-soft); margin-top: 3px; }
  .contact-address { font-size: 12px; line-height: 1.4; margin-top: 18px; }
  .contact-lines { list-style: none; font-size: 12px; line-height: 1.4; }
  .contact-lines li { display: flex; align-items: center; gap: 8px; }
  .contact-lines svg { width: 10px; height: 10px; flex: none; fill: var(--brand-red); }
</style>
</head>
<body>
  <section class="card card-back" aria-label="Business card back">
    <div class="back-wordmark">Bright Horizon<br>Guild</div>
  </section>

  <section class="card card-front" aria-label="Business card front">
    <div class="decor-circle" aria-hidden="true"></div>
    <span class="brand-dot" aria-hidden="true"></span>
    <div class="front-wordmark">Bright<br>Horizon<br>Guild</div>

    <div class="contact">
      <p class="contact-name">Neil P. Barton</p>
      <p class="contact-title">CEO</p>
      <p class="contact-address">912 North Calloway Lane<br>Beverly Hills, CA 89377</p>
      <ul class="contact-lines">
        <li>
          <svg viewBox="0 0 10 10" aria-hidden="true"><path d="M2 0h2l1 3-1.5 1a6 6 0 0 0 2.5 2.5L7 5l3 1v2c0 1-1 2-2 2A8 8 0 0 1 0 2c0-1 1-2 2-2z"/></svg>
          310-555-0182
        </li>
        <li>
          <svg viewBox="0 0 10 10" aria-hidden="true"><path d="M0 2h10v6H0z M0 2l5 3.5L10 2" stroke="#fff" stroke-width="0.8"/></svg>
          neil@brighthorizonguild.com
        </li>
        <li>
          <svg viewBox="0 0 10 10" aria-hidden="true"><circle cx="5" cy="5" r="5"/><path d="M0 5h10M5 0v10M2 2c2 1 4 1 6 0M2 8c2-1 4-1 6 0" stroke="#fff" stroke-width="0.7" fill="none"/></svg>
          www.brighthorizonguild.com
        </li>
      </ul>
    </div>
  </section>
</body>
</html>
```